Label design for organic saffron, saffron and herbal syrup

We cultivate saffron, Damszen roses, flowers and herbs. We would need a recognizable outfit (label) for our products. Theoretically (and practically) we have "converted" the family coat of arms into a kind of LOGO. I would send this in the attachment. It would be nice if - in one way or another - this LOGO / coat of arms could be used (certainly with other colors). For some time we have played with the idea of changing the second part of the family name "Wallmoser" (in German .... greuth sounds similar to Kraut / herb [English]) .... eg Wallmoser's saffron syrup into the labeling.
Our products are primarily syrups, currently herbal syrup and saffron syrup. Here the first problem arises, the only bottles / caps that are actually approved for syrup filling (hot filling) are appallingly ugly (see attachment), the only possibility of "sprucing up" is to use so-called "shrink sleeves" (here we need a diameter of 31 and a length of about 40), the colors of which are also limited. Besides the syrup, we sell saffron as a spice and various herbal mixtures (see appendix current packaging saffron). Our quantities are small (syrup 200ml-330ml), saffron in the gram range.
We also need quasi the back of the labeling (this should be able to be redefined per charge) .... Batch 1 (with small quantity has eg more of herb xy than the next batch or the saffron syrup with batch xy needs more / less saffron). In addition, we are certified organic (for this reason, the reverse side would also have to contain all the requirements of organic labeling) [see attachment].
We do not really want to address a specific clientele. Maybe just people who want to taste, enjoy, mix drinks, cook .... (and - unfortunately - don't like Corvel syrup :-) and want to pay a bit more, or find our saffron or herbs better than others) .
In summary
- Strong recognition value (possibly inclusion of "coat of arms", color variable ... although I personally don't like yellow that much)
- Saffron syrup (the color of the saffron syrup is yellow / golden-yellow-light orange, in a transparent ugly bottle)
- Herbal syrup (color variable from blue / green / brown / red elements, in transparent ugly bottle)
Saffron and other herbs (very small containers, type of container not yet fixed)
Regarding a potential "style" I can unfortunately give little information. On the one hand, I am in love with minimalism, on the other hand, I find the translucent, cryptic, implied enormously attractive and sometimes even the "overloaded" colorful has its charm. I think that all in all, it just has to be coherent, and then it will be good.
Requirements
Must have
- Integration of Code of Arms, modifiable for different products

```html
<!DOCTYPE html>
<html lang="de">
<head>
<meta charset="utf-8">
<title>Wallmoser Herbal-Sirup Lemon Balm Label</title>
<link rel="stylesheet" href="https://fonts.googleapis.com/css2?family=Fira+Sans+Condensed:wght@500;600;700&family=Exo+2:wght@600&family=Comfortaa:wght@400&family=Cormorant+Garamond:ital,wght@0,600&display=swap">
<style>
  :root {
    --paper: #ffffff;
    --forest: #0b3f25;
    --forest-deep: #08331d;
    --leaf: #8cc63f;
    --leaf-soft: #b5d98a;
    --sage: #4f7a3c;
    --navy: #2b2a6b;
    --badge: #c5e0a5;
    --badge-line: #7fb552;
  }
  * { margin: 0; padding: 0; box-sizing: border-box; }
  html, body { width: 784px; height: 1200px; overflow: hidden; background: var(--paper); }
  .label {
    position: relative;
    width: 784px;
    height: 1200px;
    background: var(--paper);
  }
  .label__panel {
    position: absolute;
    left: 45px; top: 45px;
    width: 699px; height: 1116px;
    background: var(--forest);
    overflow: hidden;
  }
  .ornament {
    position: absolute;
    top: 0;
    width: 300px; height: 355px;
    background: radial-gradient(circle at 50% 45%, rgba(120,170,80,0.28), rgba(120,170,80,0.06) 60%, transparent 75%);
  }
  .ornament--left { left: -20px; }
  .ornament--right { right: -20px; }
  .crest-tab {
    position: absolute;
    left: 297px; top: 0;
    width: 106px; height: 230px;
    background: var(--paper);
  }
  .crest-disc {
    position: absolute;
    left: 159px; top: 37px;
    width: 382px; height: 382px;
    border-radius: 50%;
    background: var(--paper);
  }
  .brand {
    position: absolute;
    left: 159px; top: 135px;
    width: 382px;
    display: flex; flex-direction: column; align-items: center; gap: 22px;
  }
  .brand__mark {
    width: 120px; height: 120px;
    border-radius: 50%;
    background: #d8d6e6;
  }
  .brand__name {
    font-family: "Cormorant Garamond", serif;
    font-weight: 600;
    font-size: 54px;
    color: var(--navy);
    letter-spacing: 1px;
  }
  .product-band {
    position: absolute;
    left: 0; top: 355px;
    width: 699px; height: 76px;
    background: var(--leaf);
    display: flex; align-items: center; justify-content: center;
  }
  .product-band__title {
    font-family: "Exo 2", sans-serif;
    font-weight: 600;
    font-size: 36px;
    letter-spacing: 2px;
    color: var(--paper);
    -webkit-text-stroke: 1.4px var(--forest);
  }
  .variety-banner {
    position: absolute;
    left: 191px; top: 433px;
    width: 290px; height: 90px;
  }
  .variety-banner svg { position: absolute; inset: 0; }
  .variety-banner__name {
    position: absolute;
    left: 0; top: 12px; width: 290px;
    text-align: center;
    font-family: "Fira Sans Condensed", sans-serif;
    font-weight: 700;
    font-size: 33px;
    color: var(--paper);
    -webkit-text-stroke: 1.2px var(--forest);
  }
  .plant-art {
    position: absolute;
    left: 228px; top: 530px;
    width: 290px; height: 480px;
    background: radial-gradient(ellipse at 45% 35%, rgba(110,160,80,0.45), rgba(80,130,60,0.18) 55%, transparent 78%);
  }
  .ingredients {
    position: absolute;
    left: -256px; top: 723px;
    width: 680px; height: 90px;
    transform: rotate(-90deg);
    font-family: "Fira Sans Condensed", sans-serif;
    font-weight: 600;
    font-size: 15.5px;
    line-height: 22px;
    color: var(--paper);
    text-align: center;
  }
  .organic-note {
    position: absolute;
    left: 405px; top: 700px;
    width: 520px; height: 30px;
    transform: rotate(90deg);
    font-family: "Fira Sans Condensed", sans-serif;
    font-weight: 600;
    font-size: 18px;
    color: var(--paper);
    text-align: center;
    letter-spacing: 0.3px;
  }
  .cert-badge {
    position: absolute;
    left: 555px; top: 783px;
    width: 86px; height: 168px;
    background: var(--badge);
    border: 1.5px solid var(--badge-line);
  }
  .cert-badge__seal {
    position: absolute;
    left: 20px; top: 10px;
    width: 46px; height: 46px;
    border-radius: 50%;
    background: var(--paper);
    border: 3px solid var(--sage);
  }
  .cert-badge__leaf {
    position: absolute;
    left: 6px; top: 68px;
    width: 72px; height: 52px;
    background: var(--leaf);
  }
  .volume {
    position: absolute;
    left: 0; top: 1028px;
    width: 699px;
    text-align: center;
    font-family: "Comfortaa", sans-serif;
    font-size: 30px;
    letter-spacing: 1px;
    color: var(--paper);
  }
</style>
</head>
<body>
<main class="label">
  <section class="label__panel">
    <div class="ornament ornament--left" role="img" aria-label="Faint green mandala ornament"></div>
    <div class="ornament ornament--right" role="img" aria-label="Faint green mandala ornament"></div>

    <div class="crest-tab"></div>
    <div class="crest-disc"></div>
    <div class="brand">
      <span class="brand__mark"></span>
      <span class="brand__name">Wallmoser</span>
    </div>

    <div class="product-band">
      <h1 class="product-band__title">HERBAL- SIRUP</h1>
    </div>

    <div class="variety-banner">
      <svg width="290" height="90" viewBox="0 0 290 90">
        <path d="M6 0 H284 V78 Q145 58 6 78 Z" fill="var(--leaf)"/>
        <rect x="0" y="0" width="4" height="80" fill="var(--paper)"/>
        <rect x="286" y="0" width="4" height="80" fill="var(--paper)"/>
      </svg>
      <h2 class="variety-banner__name">Lemon Balm</h2>
    </div>

    <div class="plant-art" role="img" aria-label="Line illustration of a flowering herb plant in soft green"></div>

    <p class="ingredients">ZUTATEN: Lorem ipsum dolor sit amet, consectetur adipiscing elit. Morbi ultricies molestie orci. Aenean purus mauris, sodales nec diam dignissim, porttitor laoreet enim. Aliquam id sollicitudin turpis. Vivamus aliquet elit sem, et ornare ex aliquam in.</p>

    <p class="organic-note">*aus kontrolliert biologischer Landwirtschaft</p>

    <div class="cert-badge" role="img" aria-label="Organic certification badge">
      <span class="cert-badge__seal"></span>
      <span class="cert-badge__leaf"></span>
    </div>

    <p class="volume">300mL</p>
  </section>
</main>
</body>
</html>
```